Health Supplement Series for 60 tablets of pure Amber Vine Core powder

We need a packaging design theme for a health supplement for international consumers. Our initial product is called 'Amber Vine Core'. It is for general health and is particularly effective for diabetic symptoms.
We would like to see designs that are clean and fresh.
It should give the impression of professional, premium pharmaceutical grade products.
Our company logo is attached below.

Target Market(s)

International

Industry/Entity Type

Health And Wellness

Font styles to use
Serif
Sans Serif

Requirements
Must have
• Bottle and box packaging required.
• 1st product is bottle of 60 tablets of 0.5gm each.
Should not have
• Seals and other "must buy" "guaranteed" etc

```html
<!DOCTYPE html>
<html lang="en">
<head>
<meta charset="utf-8">
<title>Amber Vine Core – Label</title>
<link href="https://fonts.googleapis.com/css2?family=Open+Sans:wght@400;600;700&display=swap" rel="stylesheet">
<style>
  :root {
    --bg: #efefef;
    --label: #ffffff;
    --band: #4a2210;
    --title: #5b2a14;
    --body: #555555;
    --brand: #5a9a2a;
    --art-light: #f3e6d8;
    --art-mid: #c98a55;
    --art-deep: #7a3a1a;
  }
  * { margin: 0; padding: 0; box-sizing: border-box; }
  html, body {
    width: 1158px; height: 1200px; overflow: hidden;
    background: var(--bg);
    font-family: "Open Sans", Arial, sans-serif;
  }
  .label {
    position: absolute; left: 134px; top: 50px;
    width: 890px; height: 1100px;
    background: var(--label);
    overflow: hidden;
  }
  .band-top { position: absolute; left: 0; top: 0; width: 100%; height: 16px; background: var(--band); }
  .band-bottom { position: absolute; left: 0; bottom: 0; width: 100%; height: 30px; background: var(--band); }
  .brand {
    position: absolute; left: 104px; top: 128px;
    display: flex; align-items: center; gap: 10px;
    color: var(--brand); font-weight: 600;
  }
  .brand-mark { width: 40px; height: 40px; background: var(--brand); }
  .brand-name { font-size: 26px; line-height: 1; letter-spacing: 1px; }
  .product-title {
    position: absolute; left: 98px; top: 215px;
    color: var(--title); font-weight: 700;
    font-size: 132px; line-height: 125px; letter-spacing: -1px;
  }
  .product-title span { display: block; }
  .intro {
    position: absolute; left: 104px; top: 612px; width: 330px;
    color: var(--body); font-size: 21px; line-height: 28px;
  }
  .product-art {
    position: absolute; left: 0; top: 720px; width: 890px; height: 350px;
    background: linear-gradient(180deg, var(--art-light) 0%, var(--art-mid) 60%, var(--art-deep) 100%);
  }
</style>
</head>
<body>
  <div class="label">
    <div class="band-top"></div>

    <div class="brand">
      <div class="brand-mark"></div>
      <div class="brand-name">NERALA BIOLABS LIMITED</div>
    </div>

    <h1 class="product-title"><span>AMBER</span><span>VINE</span><span>CORE</span></h1>

    <p class="intro">Lorem ipsum dolor sit amet, consectetur adipiscing elit. Ut mollis lobortis tempus. Donec</p>

    <div class="product-art" role="img" aria-label="Photograph of split brown seed pods above flowing brown ribbon artwork"></div>

    <div class="band-bottom"></div>
  </div>
</body>
</html>
```